Web Design job - Condo Debts Collection Business needs a Web Design

I need a site for a client, who works with condo debts collection, and ensure all revenues provided by condo fees will be always available to the building manager of condo on a specific date, regardless of defaults.
I have the visual identity (logo, slogan and colors) of the company, and some requirements on layout (kind of slider, menu options, phone number on a noble position, etc) - maybe I can do a sketch, but I like the idea of give some freedom to designer.

*** PLEASE, we have no interest in templates. We want something new***

Target Market(s)

I have two targets for this design: - Condominium's building manager. This target is looking for a solution to overdue debts on it's condo. - Residents on condominiums. This target wants to live in a better place, where their neighbors pay their condominium fees on time.

Number of Pages Required

1 page

Requirements
Must have
• - Slider with title, some short text related, a nice image (I prefer happy and/or peaceful family, people doing business, happy friends, and so on).
• - I have a special attention to menu. I'm looking for one I can have a nice effect, more elegant, charming, kind of innovative.
• - Phone number on the top (or clearly visible).
• - Member log in area or icon on the top (or clearly visible).
• - News/articles area.
• - Modern fonts, with good quality, sans-serif on areas where reading is more intensive (prefer Google web-fonts).
• - Colors specified on attached files.
Nice to have
• - Clear background color, cause it's better to read larger texts (like articles). Dark backgrounds makes reading difficult.
• - A site with effects (like shadows, lines, curves, gradients, lights) is usually pretty.
• - I pay attention on beautiful footers.
Should not have
• - Images with a lot of money (I don't sell richness, I sell tranquility, peace, harmony, safety).
• - Poor menu.

```html
<!DOCTYPE html>
<html lang="en">
<head>
<meta charset="utf-8">
<title>norvia — Condo Debts Collection</title>
<link href="https://fonts.googleapis.com/css2?family=Montserrat:wght@400;600;700;800&family=Open+Sans:wght@400;600;700&display=swap" rel="stylesheet">
<style>
:root{
  --gold:#e5a51b;
  --gold-light:#f1b72c;
  --gold-deep:#c98c0e;
  --ink:#262626;
  --text:#4a4a4a;
  --muted:#8a8a8a;
  --paper:#ffffff;
  --mist:#f3f1f1;
  --charcoal:#3a3a3a;
  --line:#dcdcdc;
}
*{box-sizing:border-box;margin:0;padding:0}
html,body{width:1200px;height:3982px;overflow:hidden}
body{position:relative;background:var(--paper);font-family:"Open Sans",Arial,sans-serif;color:var(--text)}
.abs{position:absolute}
h1,h2,h3,h4,.brand,.nav a,.btn{font-family:"Montserrat",Arial,sans-serif}

/* header */
.header{left:0;top:0;width:1200px;height:118px;background:var(--paper);z-index:5}
.brand{display:flex;align-items:center;gap:14px;color:var(--ink);font-weight:800;font-size:56px;letter-spacing:-1px;line-height:1}
.brand-square{width:46px;height:46px;background:var(--gold)}
.header .brand{left:130px;top:16px}
.tagline{left:192px;top:82px;font-family:"Montserrat",sans-serif;font-size:11px;font-weight:700;letter-spacing:.5px;color:var(--ink)}
.login{left:750px;top:24px;width:112px;height:30px;border:1.5px solid var(--ink);border-radius:3px;font-size:11px;font-weight:600;text-align:center;line-height:27px;color:var(--ink)}
.call{left:886px;top:18px;display:flex;gap:8px;align-items:center}
.call small{display:block;font-family:"Montserrat",sans-serif;font-size:11px;font-weight:700;color:var(--ink)}
.call strong{display:block;font-family:"Montserrat",sans-serif;font-size:22px;font-weight:700;color:var(--gold)}
.nav{left:440px;top:74px;height:38px;display:flex;align-items:center}
.nav .cap{width:0;height:0;border-left:20px solid transparent;border-right:20px solid transparent;border-top:38px solid var(--gold)}
.nav a{display:block;height:38px;line-height:38px;padding:0 24px;margin:0 -6px;background:var(--gold);color:var(--ink);font-size:11px;font-weight:700;text-decoration:none;clip-path:polygon(8px 0,100% 0,calc(100% - 8px) 100%,0 100%);border-left:2px solid var(--paper)}

/* hero */
.hero{left:0;top:118px;width:1200px;height:610px;background:linear-gradient(180deg,#4d8fd6 0%,#8fbfe8 38%,#c9dcc9 52%,#9bb24a 62%,#8a9c3e 100%)}
.hero h1{left:220px;top:225px;font-size:58px;line-height:64px;font-weight:800;color:var(--ink)}
.btn{display:inline-block;background:var(--gold);color:var(--ink);font-size:14px;font-weight:700;text-align:center;border-radius:2px}
.hero .btn{left:412px;top:380px;width:114px;height:40px;line-height:40px}
.dots{display:flex;gap:10px}
.dots i{width:9px;height:9px;border-radius:50%;background:rgba(255,255,255,.75)}
.dots i.on{background:var(--ink)}
.hero .dots{left:548px;top:630px}
.wave{left:0;width:1200px}

/* sections */
.section-title{width:1200px;left:0;text-align:center;font-size:24px;font-weight:800;color:var(--ink);letter-spacing:.5px}
.rule{left:580px;width:42px;height:4px;background:#bdbdbd;border-radius:2px}
.service{width:180px;text-align:center}
.service svg{display:block;margin:0 auto}
.service h3{font-size:14px;font-weight:700;color:var(--ink);margin:34px 0 14px}
.service p{font-size:11px;line-height:15px;color:var(--text)}

.welcome{left:0;top:1282px;width:1200px;height:552px;background:linear-gradient(90deg,var(--gold-light),var(--gold) 60%,var(--gold-deep))}
.welcome .mark{left:232px;top:1356px;width:70px;height:70px;background:var(--paper)}
.welcome h2{left:232px;top:1460px;color:var(--paper);font-weight:800}
.welcome h2 span{display:block;font-size:24px}
.welcome h2 b{display:block;font-size:56px;line-height:64px}
.welcome p{left:232px;top:1565px;width:330px;font-size:13px;line-height:15px;color:#fff5df}
.welcome .btn{left:236px;top:1700px;width:110px;height:34px;line-height:34px;background:var(--paper);color:var(--gold)}
.mosaic{left:662px;top:1380px;width:310px;height:330px;border-radius:20px;background:linear-gradient(135deg,#6f6f75,#2c2c33 50%,#8d7a5c)}

.features{left:0;top:1834px;width:1200px;height:692px;background:var(--mist)}
.feature{width:340px;height:150px;display:flex;gap:26px}
.feature svg{flex:none}
.feature h3{font-size:14px;font-weight:700;color:var(--ink);margin:4px 0 6px}
.feature p{font-size:11px;line-height:15px}
.fdiv-v{left:580px;top:2040px;width:1px;height:398px;background:var(--line)}
.fdiv-h{height:1px;background:var(--line)}

.card{top:2735px;width:440px;height:225px;background:var(--mist);display:flex;padding:12px 20px 12px 18px;gap:28px}
.card .thumb{width:185px;height:198px;flex:none}
.card h3{font-size:15px;line-height:19px;font-weight:700;color:var(--ink);margin-top:30px}
.card p{font-size:11px;line-height:14px;margin-top:14px}
.card .btn{position:absolute;right:20px;bottom:18px;width:74px;height:24px;line-height:24px;font-size:10px}
.arrow{top:2830px}

.testimonials{left:0;top:3052px;width:1200px;height:540px;background:var(--charcoal)}
.testimonials .section-title{color:var(--paper);top:96px}
.avatar{left:298px;top:3290px;width:124px;height:124px;border-radius:50%;background:linear-gradient(135deg,#b89a78,#4a3b31)}
.quote p{font-size:15px;line-height:19px;color:#eaeaea}
.quote h4{margin-top:22px;font-size:12px;font-weight:700;color:var(--paper)}

.footer{left:0;top:3560px;width:1200px;height:422px;background:var(--gold)}
.footer .brand{left:130px;top:3655px;font-size:60px}
.footer .brand .brand-square{background:var(--paper)}
.footer .tagline{left:192px;top:3725px;font-size:12px}
.fcol h4{font-family:"Montserrat",sans-serif;font-size:11px;font-weight:700;color:var(--ink);margin-bottom:20px}
.fcol li{list-style:none;font-size:11px;color:var(--ink);line-height:14px;display:flex;gap:10px;align-items:flex-start;margin-bottom:14px}
.fcol.menu li{margin:0}
.social li{align-items:center}
.social .dot{width:28px;height:28px;border-radius:50%;background:var(--charcoal);flex:none}
.frule{left:130px;top:3897px;width:940px;height:1px;background:rgba(0,0,0,.2)}
.copy{left:0;top:3920px;width:1200px;text-align:center;font-size:11px;color:var(--ink)}
</style>
</head>
<body>

<header class="header abs">
  <div class="brand abs"><span class="brand-square"></span>norvia</div>
  <div class="tagline abs">COBRANÇA CONDOMINIAL</div>
  <div class="login abs">Member Log In</div>
  <div class="call abs">
    <svg width="24" height="30" viewBox="0 0 24 30"><path d="M6 3l5 6-3 3c2 5 5 8 9 10l3-3 5 5-4 4C12 27 2 17 2 7z" fill="none" stroke="var(--gold)" stroke-width="2"/></svg>
    <div><small>CALL US</small><strong>555.010.2040</strong></div>
  </div>
  <nav class="nav abs">
    <span class="cap"></span>
    <a>HOME</a><a>ABOUT US</a><a>SERVICES</a><a>BENEFITS</a><a>BLOG</a><a>CONTACT US</a>
    <span class="cap"></span>
  </nav>
</header>

<section class="hero abs" role="img" aria-label="Happy family in a green field under a blue sky, father carrying a child on his shoulders"></section>
<h1 class="abs" style="left:220px;top:225px;font-size:58px;line-height:64px;font-weight:800;color:var(--ink)">DEBTS<br>Collection</h1>
<span class="btn abs" style="left:412px;top:380px;width:114px;height:40px;line-height:40px">Read More</span>
<div class="dots abs" style="left:548px;top:628px"><i></i><i></i><i class="on"></i><i></i><i></i></div>
<svg class="wave abs" style="top:640px" width="1200" height="100" viewBox="0 0 1200 100" preserveAspectRatio="none">
  <path d="M0 60 Q300 100 650 70 T1200 20 V100 H0Z" fill="var(--paper)"/>
  <path d="M0 60 Q300 100 650 70 T1200 20" fill="none" stroke="var(--gold)" stroke-width="6"/>
</svg>

<h2 class="section-title abs" style="top:800px">OUR SERVICES</h2>
<div class="rule abs" style="top:854px"></div>

<div class="service abs" style="left:109px;top:948px">
  <svg width="130" height="116" viewBox="0 0 130 116"><path d="M65 0L130 116H0Z" fill="var(--gold)"/><circle cx="65" cy="76" r="17" fill="none" stroke="#fff" stroke-width="4"/><text x="65" y="83" font-size="18" font-weight="700" fill="#fff" text-anchor="middle" font-family="Montserrat">$</text></svg>
  <h3>Debt Collector</h3><p>Lorem ipsum is simply a sample text of the print and typesetting trade now used as their default mode.</p>
</div>
<div class="service abs" style="left:300px;top:948px">
  <svg width="130" height="116" viewBox="0 0 130 116"><path d="M0 0H130L65 116Z" fill="var(--gold)"/><rect x="50" y="22" width="30" height="38" fill="none" stroke="#fff" stroke-width="4"/><path d="M56 50l7-9 6 6 5-8" fill="none" stroke="#fff" stroke-width="3"/></svg>
  <h3>Credit Report</h3><p>Lorem ipsum is simply a sample text of the print and typesetting trade now used as their default mode.</p>
</div>
<div class="service abs" style="left:507px;top:948px">
  <svg width="130" height="116" viewBox="0 0 130 116"><path d="M65 0L130 116H0Z" fill="var(--gold)"/><rect x="50" y="62" width="13" height="13" fill="#fff"/><rect x="67" y="62" width="13" height="13" fill="#fff"/><rect x="67" y="79" width="13" height="13" fill="#fff"/><rect x="50" y="79" width="13" height="13" fill="none" stroke="#fff" stroke-width="3"/></svg>
  <h3>Disputing Collections</h3><p>Lorem ipsum is simply a sample text of the print and typesetting trade now used as their default mode.</p>
</div>
<div class="service abs" style="left:696px;top:948px">
  <svg width="130" height="116" viewBox="0 0 130 116"><path d="M0 0H130L65 116Z" fill="var(--gold)"/><circle cx="65" cy="38" r="9" fill="none" stroke="#fff" stroke-width="3"/><circle cx="44" cy="22" r="5" fill="#fff"/><circle cx="86" cy="22" r="5" fill="#fff"/><circle cx="44" cy="54" r="5" fill="#fff"/><circle cx="86" cy="54" r="5" fill="#fff"/></svg>
  <h3>Debt Settlement</h3><p>Lorem ipsum is simply a sample text of the print and typesetting trade now used as their default mode.</p>
</div>
<div class="service abs" style="left:908px;top:948px">
  <svg width="130" height="116" viewBox="0 0 130 116"><path d="M65 0L130 116H0Z" fill="var(--gold)"/><path d="M45 72l20-18 20 18" fill="none" stroke="#fff" stroke-width="4"/><rect x="52" y="72" width="26" height="20" fill="#fff"/></svg>
  <h3>Mortgage Help</h3><p>Lorem ipsum is simply a sample text of the print and typesetting trade now used as their default mode.</p>
</div>

<section class="welcome abs"></section>
<div class="mark abs" style="left:232px;top:1356px;width:70px;height:70px;background:var(--paper)"></div>
<h2 class="abs" style="left:232px;top:1460px;color:var(--paper);font-weight:800"><span style="display:block;font-size:24px">WELCOME TO</span><b style="display:block;font-size:56px;line-height:64px">NORVIA.</b></h2>
<p class="abs" style="left:232px;top:1565px;width:330px;font-size:13px;line-height:15px;color:#fff5df">But I must explain to you how this mistaken idea of denouncing pleasure and praising pain was born and I will give you a complete account of the system, and expound the actual teachings of the great explorer of the truth, the master builder of human happiness. No one rejects, dislikes.</p>
<span class="btn abs" style="left:236px;top:1700px;width:110px;height:34px;line-height:34px;background:var(--paper);color:var(--gold)">Read More</span>
<div class="mosaic abs" role="img" aria-label="Collage of business people shaking hands and working in an office"></div>

<section class="features abs"></section>
<h2 class="section-title abs" style="top:1910px">FEATURES</h2>
<div class="rule abs" style="top:1964px"></div>
<div class="fdiv-v abs"></div>
<div class="fdiv-h abs" style="left:200px;top:2170px;width:380px"></div>
<div class="fdiv-h abs" style="left:580px;top:2170px;width:380px"></div>
<div class="fdiv-h abs" style="left:200px;top:2318px;width:380px"></div>
<div class="fdiv-h abs" style="left:580px;top:2318px;width:380px"></div>

<div class="feature abs" style="left:200px;top:2045px">
  <svg width="48" height="48" viewBox="0 0 48 48"><rect x="6" y="12" width="36" height="28" rx="2" fill="var(--gold)"/><rect x="12" y="6" width="24" height="8" fill="var(--gold-deep)"/><path d="M12 22h24M12 29h18" stroke="#fff" stroke-width="3"/></svg>
  <div><h3>Customized Collection Letters</h3><p>Lorem ipsum is simply a sample text of the print and typesetting trade now used as their default mode. Neque porro quisquam est, qui dolorem.</p></div>
</div>
<div class="feature abs" style="left:620px;top:2045px">
  <svg width="48" height="48" viewBox="0 0 48 48"><circle cx="24" cy="24" r="20" fill="var(--gold)"/><circle cx="24" cy="24" r="10" fill="none" stroke="#fff" stroke-width="3"/><path d="M19 24l4 4 6-7" fill="none" stroke="#fff" stroke-width="3"/></svg>
  <div><h3>Client Satisfaction</h3><p>Lorem ipsum is simply a sample text of the print and typesetting trade now used as their default mode. Neque porro quisquam est, qui dolorem.</p></div>
</div>
<div class="feature abs" style="left:200px;top:2195px">
  <svg width="48" height="48" viewBox="0 0 48 48"><circle cx="20" cy="20" r="13" fill="none" stroke="var(--gold)" stroke-width="5"/><path d="M30 30l12 12" stroke="var(--gold)" stroke-width="6" stroke-linecap="round"/></svg>
  <div><h3>No Fine Print</h3><p>Lorem ipsum is simply a sample text of the print and typesetting trade now used as their default mode. Neque porro quisquam est, qui dolorem.</p></div>
</div>
<div class="feature abs" style="left:620px;top:2195px">
  <svg width="48" height="48" viewBox="0 0 48 48"><circle cx="24" cy="16" r="9" fill="none" stroke="var(--gold)" stroke-width="3"/><path d="M10 44c0-10 6-16 14-16s14 6 14 16z" fill="var(--gold)"/><path d="M13 16a11 11 0 0 1 22 0" fill="none" stroke="var(--gold-deep)" stroke-width="3"/></svg>
  <div><h3>Debt Collection Call Center</h3><p>Lorem ipsum is simply a sample text of the print and typesetting trade now used as their default mode. Neque porro quisquam est, qui dolorem.</p></div>
</div>
<div class="feature abs" style="left:200px;top:2345px">
  <svg width="48" height="48" viewBox="0 0 48 48"><path d="M24 4l18 6v12c0 12-8 19-18 22C14 41 6 34 6 22V10z" fill="var(--gold)"/><path d="M16 24l6 6 10-11" fill="none" stroke="#fff" stroke-width="4"/></svg>
  <div><h3>Secure Collections</h3><p>Lorem ipsum is simply a sample text of the print and typesetting trade now used as their default mode. Neque porro quisquam est, qui dolorem.</p></div>
</div>
<div class="feature abs" style="left:620px;top:2345px">
  <svg width="48" height="48" viewBox="0 0 48 48"><rect x="10" y="4" width="28" height="40" rx="2" fill="var(--gold)"/><path d="M16 16h16M16 23h16M16 30h10" stroke="#fff" stroke-width="3"/></svg>
  <div><h3>Free Business Reports</h3><p>Lorem ipsum is simply a sample text of the print and typesetting trade now used as their default mode. Neque porro quisquam est, qui dolorem.</p></div>
</div>

<h2 class="section-title abs" style="top:2604px">LATEST NEWS</h2>
<div class="rule abs" style="top:2656px"></div>
<svg class="arrow abs" style="left:80px" width="16" height="30" viewBox="0 0 16 30"><path d="M13 3L3 15l10 12" fill="none" stroke="var(--muted)" stroke-width="2.5"/></svg>
<svg class="arrow abs" style="left:1104px" width="16" height="30" viewBox="0 0 16 30"><path d="M3 3l10 12L3 27" fill="none" stroke="var(--muted)" stroke-width="2.5"/></svg>
<article class="card abs" style="left:145px">
  <div class="thumb" role="img" aria-label="Businessman working at a laptop in a dim office" style="background:linear-gradient(135deg,#6c7078,#2a2d33)"></div>
  <div><h3>Sed ut perspiciatis unde omnis iste</h3><p>Lorem ipsum is simply a sample text of the print and typesetting trade now used as their default mode.</p></div>
  <span class="btn">Read More</span>
</article>
<article class="card abs" style="left:620px">
  <div class="thumb" role="img" aria-label="Two business colleagues reviewing a tablet together" style="background:linear-gradient(135deg,#c8c8c8,#3c4350)"></div>
  <div><h3>Sed ut perspiciatis unde omnis iste</h3><p>Lorem ipsum is simply a sample text of the print and typesetting trade now used as their default mode.</p></div>
  <span class="btn">Read More</span>
</article>

<section class="testimonials abs">
  <h2 class="section-title abs">TESTIMONIALS</h2>
  <div class="rule abs" style="top:148px;background:#dcdcdc"></div>
</section>
<div class="avatar abs" role="img" aria-label="Portrait of a client"></div>
<svg class="abs" style="left:395px;top:3282px" width="44" height="36" viewBox="0 0 44 36"><path d="M2 36V18C2 8 8 2 18 0v6c-5 2-8 6-8 12h8v18zM26 36V18c0-10 6-16 16-18v6c-5 2-8 6-8 12h8v18z" fill="var(--gold)"/></svg>
<div class="quote abs" style="left:480px;top:3280px;width:450px">
  <p>At vero eos et accusamus et iusto odio dignissimos ducimus qui blanditiis praesentium voluptatum deleniti atque corrupti quos dolores et quas molestias excepturi sint occaecati cupiditate non provident, similique sunt in culpa qui officia deserunt mollitia animi, id est laborum et dolorum fuga</p>
  <h4>DANIEL</h4>
</div>
<div class="dots abs" style="left:834px;top:3456px"><i style="background:#bbb"></i><i style="background:#bbb"></i><i style="background:var(--gold)"></i><i style="background:#bbb"></i></div>

<svg class="wave abs" style="top:3520px" width="1200" height="90" viewBox="0 0 1200 90" preserveAspectRatio="none">
  <path d="M0 10 Q350 70 700 45 T1200 20 V90 H0Z" fill="var(--gold)"/>
  <path d="M0 10 Q350 70 700 45 T1200 20" fill="none" stroke="var(--gold-light)" stroke-width="5"/>
</svg>
<footer class="footer abs"></footer>
<div class="brand abs" style="left:130px;top:3655px;font-size:60px"><span class="brand-square" style="background:var(--paper)"></span>norvia</div>
<div class="tagline abs" style="left:192px;top:3725px;font-size:12px">COBRANÇA CONDOMINIAL</div>

<div class="fcol abs" style="left:510px;top:3660px">
  <h4>CONTACT US</h4>
  <ul>
    <li><svg width="10" height="14" viewBox="0 0 10 14"><path d="M5 0a5 5 0 0 1 5 5c0 4-5 9-5 9S0 9 0 5a5 5 0 0 1 5-5z" fill="var(--ink)"/></svg><span>48 Harbor Lane<br>Millbrook, IL 60100</span></li>
    <li><svg width="12" height="12" viewBox="0 0 12 12"><path d="M2 0l3 3-1.5 2c1 2 2 3 3.5 3.5L9 7l3 3-2 2C5 12 0 7 0 2z" fill="var(--ink)"/></svg><span>555.010.2040</span></li>
    <li><svg width="13" height="10" viewBox="0 0 13 10"><rect width="13" height="10" fill="var(--ink)"/><path d="M0 0l6.5 5L13 0" fill="none" stroke="var(--gold)" stroke-width="1.3"/></svg><span>info@norvia.com</span></li>
  </ul>
</div>
<div class="fcol menu abs" style="left:744px;top:3660px">
  <h4>MENU</h4>
  <ul><li>HOME</li><li>ABOUT US</li><li>SERVICES</li><li>BENEFITS</li><li>BLOG</li><li>CONTACT US</li></ul>
</div>
<div class="fcol social abs" style="left:934px;top:3660px">
  <h4>CONNECT WITH US</h4>
  <ul>
    <li><span class="dot"></span>Community</li>
    <li><span class="dot"></span>Updates</li>
    <li><span class="dot"></span>Network</li>
  </ul>
</div>
<div class="frule abs"></div>
<div class="copy abs">Copyrights @ 2016 All Rights Reserved</div>

</body>
</html>
```